Im open to ideas.. I was thinking on my business cards aswell as my logo. a place for my name. email. phone number and abn..

ive attched a file with my business logo. which i dont love the colours.. i was think a dark background with charcoal letters so something along those colour schumes but im open to ideas..

BRM Constructions

```html
<!DOCTYPE html>
<html lang="en">
<head>
<meta charset="UTF-8">
<title>BRM Constructions – Business Cards</title>
<link rel="stylesheet" href="https://fonts.googleapis.com/css2?family=Arimo:wght@400;700&display=swap">
<style>
  :root {
    --page-bg: #d9d6d2;
    --card-black: #151515;
    --card-edge: #0b0b0b;
    --charcoal: #3a3a3a;
    --white: #f4f4f4;
    --soft-white: #d8d8d8;
    --accent-red: #e0191f;
    --divider: #8a8a8a;
  }
  * { margin: 0; padding: 0; box-sizing: border-box; }
  html, body {
    width: 1200px;
    height: 787px;
    overflow: hidden;
    background: var(--page-bg);
    font-family: "Arimo", Arial, sans-serif;
  }
  .canvas {
    position: relative;
    width: 1200px;
    height: 787px;
  }
  .card {
    position: absolute;
    top: 238px;
    width: 540px;
    height: 310px;
    background: var(--card-black);
    border: 1px solid var(--card-edge);
    box-shadow: 0 10px 24px rgba(0,0,0,0.25);
  }
  .card-back { left: 40px; }
  .card-front { left: 620px; }

  /* Back */
  .back-brand {
    position: absolute;
    left: 0; right: 0;
    top: 104px;
    text-align: center;
    color: var(--charcoal);
    font-weight: 700;
    font-size: 40px;
    letter-spacing: 1px;
  }
  .back-web {
    position: absolute;
    left: 0; right: 0;
    top: 212px;
    text-align: center;
    color: var(--soft-white);
    font-size: 13px;
    letter-spacing: 4px;
  }

  /* Front */
  .front-brand {
    position: absolute;
    left: 34px;
    top: 132px;
    width: 270px;
    color: var(--white);
    font-weight: 700;
    font-size: 30px;
    line-height: 1.1;
  }
  .divider {
    position: absolute;
    left: 322px;
    top: 70px;
    width: 1px;
    height: 190px;
    background: var(--divider);
  }
  .contact {
    position: absolute;
    left: 342px;
    top: 108px;
    color: var(--soft-white);
    font-size: 14px;
  }
  .contact-name {
    color: var(--accent-red);
    font-weight: 700;
    font-size: 17px;
    letter-spacing: 0.5px;
  }
  .contact-title {
    color: var(--white);
    font-size: 15px;
    margin-bottom: 10px;
  }
  .contact-line {
    display: flex;
    align-items: center;
    gap: 8px;
    margin-top: 7px;
  }
  .contact-line svg { width: 13px; height: 13px; flex: none; }
  .icon-gap { padding-left: 0; }
</style>
</head>
<body>
<main class="canvas">
  <section class="card card-back" aria-label="Business card back">
    <div class="back-brand">BRM Constructions</div>
    <div class="back-web">www.brmbuild.com</div>
  </section>

  <section class="card card-front" aria-label="Business card front">
    <div class="front-brand">BRM Constructions</div>
    <div class="divider"></div>
    <div class="contact">
      <div class="contact-name">Sam Carter</div>
      <div class="contact-title">President</div>
      <div class="contact-line">ABN: 246813579</div>
      <div class="contact-line">
        <svg viewBox="0 0 24 24" aria-hidden="true"><path fill="var(--accent-red)" d="M6.6 10.8a15.1 15.1 0 0 0 6.6 6.6l2.2-2.2c.3-.3.7-.4 1-.2 1.1.4 2.3.6 3.6.6.6 0 1 .4 1 1V20c0 .6-.4 1-1 1A17 17 0 0 1 3 4c0-.6.4-1 1-1h3.5c.6 0 1 .4 1 1 0 1.3.2 2.5.6 3.6.1.3 0 .7-.2 1z"/></svg>
        <span>555 0142 7788</span>
      </div>
      <div class="contact-line">
        <svg viewBox="0 0 24 24" aria-hidden="true"><path fill="var(--accent-red)" d="M2 5h20v14H2z"/><path fill="none" stroke="var(--card-black)" stroke-width="1.8" d="M2.5 5.5 12 13l9.5-7.5"/></svg>
        <span>sam@brmbuild.com</span>
      </div>
    </div>
  </section>
</main>
</body>
</html>
```